Canyon Leaf Facial Oil and Body Oil Packaging Project

We need a packaging concept for a Hemp based facial oil and body oil. We need label design for the bottle and carton graphics. I am attaching a few reference photos. The target demographic is women between 17-35 year old. Products need to be able to stand out in crowded stores with clear calls to action.
1oz Dropper Bottle with Unit Carton - Hemp Facial Oil
4oz PET Bottle with Unit Carton - Hemp + Rose Facial Oil

```html
<!DOCTYPE html>
<html lang="en">
<head>
<meta charset="utf-8">
<title>Canyon Leaf – Facial Oil Packaging</title>
<link rel="stylesheet" href="https://fonts.googleapis.com/css2?family=Open+Sans:wdth,wght@75..100,300..700&display=swap">
<style>
  :root {
    --bg-top: #f0f0f0;
    --bg-bottom: #c9c9c9;
    --carton: #ffffff;
    --brand-green: #4c7d3a;
    --ink: #2d2d2d;
    --label-green: #2a5e22;
    --label-green-dark: #1c4313;
    --leaf-light: #8cbf5a;
    --leaf-dark: #2f6b22;
    --fade-green: #b9cfa5;
    --white: #ffffff;
  }
  * { box-sizing: border-box; margin: 0; padding: 0; }
  html, body { width: 1200px; height: 1200px; overflow: hidden; }
  body {
    background: linear-gradient(180deg, var(--bg-top), var(--bg-bottom));
    font-family: "Open Sans", sans-serif;
    color: var(--ink);
    position: relative;
  }

  /* Carton side panel */
  .carton-side {
    position: absolute; left: 90px; top: 130px; width: 170px; height: 930px;
    background: var(--carton);
    box-shadow: 0 10px 30px rgba(0,0,0,.12);
    padding: 70px 14px 0;
    font-stretch: 75%;
  }
  .carton-side .brand {
    color: var(--brand-green); font-size: 30px; font-weight: 400;
    text-align: center; line-height: 1.1;
  }
  .carton-side .blurb {
    margin-top: 110px; font-size: 12.5px; line-height: 2.3; text-align: center;
    font-weight: 400; color: var(--ink);
  }
  .carton-side .side-foot {
    position: absolute; left: 10px; right: 10px; bottom: 26px; height: 430px;
    border-radius: 0 0 10px 10px;
    background: linear-gradient(180deg, rgba(255,255,255,0), var(--fade-green));
  }
  .carton-side .side-leaf {
    position: absolute; left: 50px; top: 10px; width: 96px; height: 290px;
    border-radius: 50% 50% 10% 10%;
    background: linear-gradient(180deg, var(--leaf-light), var(--leaf-dark));
    opacity: .85;
  }
  .carton-side .side-name {
    position: absolute; left: 6px; bottom: 56px; font-size: 30px; font-weight: 400;
  }
  .carton-side .side-size {
    position: absolute; left: 6px; bottom: 22px; font-size: 22px; font-weight: 400;
  }

  /* Carton front panel */
  .carton-front {
    position: absolute; left: 262px; top: 130px; width: 400px; height: 930px;
    background: var(--carton);
    box-shadow: 0 10px 30px rgba(0,0,0,.14);
    font-stretch: 75%;
  }
  .carton-front .brand {
    position: absolute; left: 34px; top: 110px; right: 20px;
    color: var(--brand-green); font-size: 64px; font-weight: 400; line-height: 1.05;
  }
  .carton-front .product-name {
    position: absolute; left: 34px; top: 420px; font-size: 52px; font-weight: 400; line-height: 1;
  }
  .carton-front .product-sub {
    position: absolute; left: 34px; top: 484px; font-size: 32px; font-weight: 400;
  }
  .carton-front .front-leaf {
    position: absolute; left: 200px; top: 500px; width: 180px; height: 290px;
    border-radius: 50% 50% 30% 30%;
    background: radial-gradient(ellipse at 55% 45%, var(--leaf-light), var(--leaf-dark) 80%);
  }
  .carton-front .size {
    position: absolute; left: 34px; bottom: 60px; font-size: 50px; font-weight: 400;
  }

  /* Bottle label */
  .bottle-label {
    position: absolute; left: 720px; top: 400px; width: 420px; height: 470px;
    background: var(--white);
    box-shadow: 0 10px 30px rgba(0,0,0,.14);
    overflow: hidden;
  }
  .bottle-label .label-head {
    position: relative; height: 140px;
    background: linear-gradient(90deg, var(--white) 55%, #e6e6e6);
  }
  .bottle-label .head-leaf {
    position: absolute; left: 14px; top: 24px; width: 150px; height: 90px;
    border-radius: 50%;
    background: radial-gradient(ellipse, var(--leaf-light), var(--leaf-dark) 70%, rgba(47,107,34,0) 72%);
  }
  .bottle-label .brand {
    position: absolute; left: 180px; top: 48px;
    color: var(--brand-green); font-size: 36px; font-weight: 400;
  }
  .bottle-label .label-band {
    position: relative; height: 330px; padding: 26px 32px;
    background: linear-gradient(90deg, var(--label-green), var(--label-green-dark));
    color: var(--white);
  }
  .bottle-label .product-name {
    font-size: 50px; font-weight: 400; line-height: 1.2;
  }
  .bottle-label .product-sub { font-size: 25px; font-weight: 400; margin-top: 4px; }
  .bottle-label .mini-leaf {
    position: absolute; left: 32px; top: 218px; width: 46px; height: 46px;
    border-radius: 50%; background: var(--leaf-dark);
  }
  .bottle-label .size { position: absolute; left: 32px; bottom: 34px; font-size: 25px; }
  .bottle-label .drop { position: absolute; right: 40px; top: 30px; }
</style>
</head>
<body>

  <section class="carton-side">
    <p class="brand">Canyon Leaf</p>
    <p class="blurb">Lorem Ipsum is simply dummy text of the printing and typesetting industry. Lorem Ipsum has been the industry's standard dummy text ever since the 1500s, when an unknown printer took a galley of type and scrambled it to make a type specimen book.</p>
    <div class="side-foot">
      <div class="side-leaf" role="img" aria-label="Green hemp leaf illustration"></div>
      <p class="side-name">FACIAL OIL</p>
      <p class="side-size">1 oz 30 ml</p>
    </div>
  </section>

  <section class="carton-front">
    <h1 class="brand">Canyon Leaf</h1>
    <p class="product-name">FACIAL OIL</p>
    <p class="product-sub">with Hemp</p>
    <div class="front-leaf" role="img" aria-label="Large green hemp leaf illustration"></div>
    <p class="size">1 oz 30 ml</p>
  </section>

  <section class="bottle-label">
    <div class="label-head">
      <div class="head-leaf" role="img" aria-label="Green hemp leaf illustration"></div>
      <p class="brand">Canyon Leaf</p>
    </div>
    <div class="label-band">
      <p class="product-name">FACIAL<br>OIL</p>
      <p class="product-sub">with Hemp</p>
      <div class="mini-leaf" role="img" aria-label="Small hemp leaf icon"></div>
      <p class="size">1 oz 30 ml</p>
      <svg class="drop" width="140" height="210" viewBox="0 0 140 210" aria-hidden="true">
        <path d="M70 6 C 78 70, 134 100, 134 146 A 64 60 0 0 1 6 146 C 6 100, 62 70, 70 6 Z"
              fill="none" stroke="#ffffff" stroke-width="2"/>
        <path d="M26 150 A 44 44 0 0 0 58 188" fill="none" stroke="#ffffff" stroke-width="2"/>
      </svg>
    </div>
  </section>

</body>
</html>
```